National Water and Fire Restoration, Multi Surface Cleaning, Carpet Cleaning Business Needs a Websi

We need a new fresh website for our business. There are multiple services we offer and we need a fresh corporate website that represents us better. We start from cleaning carpet and tiles, to upholstery and curtains, to completely clean all contents and building materials after a fire, or completely dry out a home or business after a major or minor flood event. We are open to all concepts as we want to create a new look, maybe even logo, signage, vehicle signage, uniforms.
We are open to new colours etc.

Go to www.brightvaleclean.com.au for current logo and all other past ideas

Reason: I need to see more quality designs to sink my teeth into

Target Market(s)

The target market is everyone of all walks of life

Industry/Entity Type

Business

Number of Pages Required

3 page

Font styles to use
Sans Serif

Requirements
Must have
• Home page
• Services page
• Contact us page
• The rest is up to your imagination
• ***This is design only - NO CODING REQUIRED***
Nice to have
• Pictures

```html
<!DOCTYPE html>
<html lang="en">
<head>
<meta charset="utf-8">
<title>Brightvale Clean</title>
<link href="https://fonts.googleapis.com/css2?family=Dosis:wght@300;500;600;700&family=Open+Sans:wght@400;600&display=swap" rel="stylesheet">
<style>
:root{
  --blue:#1f5a9c;
  --navy:#1d4a80;
  --pink:#d81e7a;
  --ink:#333;
  --muted:#666;
  --grey:#e6e6e6;
  --fb:#2d4e9a;
  --white:#fff;
}
*{margin:0;padding:0;box-sizing:border-box}
html,body{width:1200px;height:2287px;overflow:hidden}
body{position:relative;background:var(--white);font-family:"Open Sans",sans-serif;color:var(--ink)}
.abs{position:absolute}
.hero-photo{left:0;top:0;width:1200px;height:676px;background:linear-gradient(160deg,#e9e2d6 0%,#c7b9a5 45%,#6fa3b5 70%,#e8e0d4 100%)}
.header-bar{left:70px;top:0;width:1060px;height:102px}
.brand{left:140px;top:30px;display:flex;align-items:center;gap:10px;font-family:"Dosis",sans-serif;font-weight:700;font-size:24px;line-height:40px;color:var(--blue);white-space:nowrap}
.brand .dot{width:40px;height:40px;border-radius:50%;background:var(--pink);flex:none}
.nav{left:416px;top:40px;display:flex;gap:24px;font-size:14px;line-height:20px;color:#222;white-space:nowrap}
.nav .active{color:var(--blue)}
.arrow{top:320px;width:24px;height:44px}
.caption{left:0;top:580px;width:1200px;height:92px;background:rgba(70,70,70,.6);text-align:center;color:var(--white);font-family:"Dosis",sans-serif}
.caption .l1{font-size:38px;font-weight:300;line-height:46px;padding-top:4px}
.caption .l1 b{color:var(--pink);font-weight:500}
.caption .l2{font-size:36px;font-weight:600;line-height:38px}
.service-area{left:0;top:640px;width:1200px;height:100px}
.service-text{left:0;top:692px;width:1200px;text-align:center;color:var(--white);font-family:"Dosis",sans-serif;font-size:17px;font-weight:500;letter-spacing:.5px}
h2.sec{position:absolute;left:0;width:1200px;text-align:center;font-family:"Dosis",sans-serif;font-weight:600;font-size:28px;color:var(--navy)}
h2.sec span{color:var(--pink)}
.view-all{left:975px;top:776px;font-size:12px;font-weight:600;color:#666}
.card{top:800px;width:300px;text-align:center}
.card .icon{width:120px;height:120px;border-radius:50%;background:#ececec;margin:27px auto 0;display:flex;align-items:center;justify-content:center}
.card .icon i{display:block;width:64px;height:40px;border-radius:4px}
.card h3{margin-top:32px;font-family:"Dosis",sans-serif;font-size:20px;font-weight:600;color:var(--navy);letter-spacing:.5px}
.card p{margin:14px auto 0;width:270px;font-size:12px;line-height:23px;color:var(--muted)}
.divider{top:800px;width:1px;height:310px;background:linear-gradient(#fff,#e4e4e4,#fff)}
.signup{left:0;top:1133px;width:1200px;height:140px;background:var(--grey);text-align:center}
.signup p{padding-top:22px;font-family:"Dosis",sans-serif;font-weight:300;font-size:29px;color:#333}
.btn{display:inline-block;background:var(--blue);color:var(--white);font-family:"Dosis",sans-serif;font-size:18px;padding:8px 22px;border:1px solid #174a82}
.signup .btn{margin-top:16px}
.social-box{left:140px;top:1308px;width:440px;height:122px;background:var(--fb);color:var(--white);display:flex;align-items:center}
.social-box .sq{width:44px;height:44px;background:var(--white);margin-left:22px;flex:none}
.social-box .find{margin-left:20px;font-family:"Dosis",sans-serif;font-weight:700;font-size:22px;line-height:26px;width:150px}
.social-box .sep{width:1px;height:76px;background:rgba(255,255,255,.7)}
.social-box .offer{margin-left:16px;font-size:13px;line-height:24px}
.news{left:619px;top:1308px;width:441px;height:122px;background:var(--pink);color:var(--white)}
.news h4{position:absolute;left:38px;top:26px;font-family:"Dosis",sans-serif;font-size:18px;font-weight:600}
.news .field{position:absolute;left:38px;top:64px;width:265px;height:36px;border:1px solid rgba(255,255,255,.8);font-size:12px;padding:9px 12px}
.news .send{position:absolute;left:320px;top:64px;width:80px;height:38px;background:#222;border-radius:4px;text-align:center;line-height:38px;font-size:14px;font-weight:600}
.about{left:150px;top:1525px;width:902px;text-align:center;font-size:11.5px;line-height:24px;color:#444}
.tile{top:1687px;width:214px;height:170px;box-shadow:0 6px 10px rgba(0,0,0,.25);border:3px solid #eee}
.tile .tl{position:absolute;left:0;width:100%;text-align:center;color:var(--white);font-family:"Dosis",sans-serif;font-weight:600;font-size:16px;line-height:20px;text-shadow:0 1px 2px rgba(0,0,0,.5)}
.tile .btn{position:absolute;left:50%;transform:translateX(-50%);top:120px;font-size:13px;padding:4px 14px;border-radius:3px;font-family:"Open Sans",sans-serif;white-space:nowrap}
.footer-top{left:0;top:1912px;width:1200px;height:261px;background:var(--grey)}
.badge-sq{left:142px;top:1944px;width:160px;height:160px;background:#2f8a2f;border-radius:4px}
.badge-cap{left:142px;top:2110px;width:160px;text-align:center;font-size:22px;color:#2f8a2f}
.badge-seal{left:362px;top:1950px;width:160px;height:160px;border-radius:50%;background:radial-gradient(circle,#d22 40%,#9b1010 100%)}
.contact{left:530px;top:1950px;width:206px;text-align:right;font-size:12px;line-height:24.5px;color:#333;white-space:nowrap}
.f-brand{left:790px;top:1962px;font-family:"Dosis",sans-serif;font-weight:700;font-size:30px;color:var(--blue);display:flex;align-items:center;gap:14px;white-space:nowrap}
.f-brand .dot{width:60px;height:60px;border-radius:50%;background:var(--pink);flex:none}
.tagline{left:790px;top:2045px;font-family:"Dosis",sans-serif;font-size:16px;color:var(--pink)}
.partners{left:790px;top:2072px;display:flex;gap:14px}
.partners i{display:block;width:56px;height:38px;background:var(--blue);border-radius:3px}
.partners i:nth-child(2){width:38px;border-radius:50%;background:#2a9ad6}
.partners i:nth-child(3){width:38px;background:#4a6fb0}
.partners i:nth-child(4){width:38px;border-radius:50%;background:#c23}
.footer-bottom{left:0;top:2173px;width:1200px;height:114px;background:var(--blue);text-align:center;color:var(--white)}
.footer-bottom p{padding-top:30px;font-size:11.5px;font-weight:600}
.socials{margin-top:14px;display:flex;gap:8px;justify-content:center}
.socials i{display:block;width:30px;height:30px;border:1.5px solid var(--white);border-radius:50%}
</style>
</head>
<body>

<div class="abs hero-photo" role="img" aria-label="Smiling family lying together on a freshly cleaned plush carpet in a bright living room"></div>

<svg class="abs header-bar" viewBox="0 0 1060 102" aria-hidden="true">
  <polygon points="0,0 1060,0 1000,102 60,102" fill="#fff" stroke="#c9c9c9" stroke-width="2"/>
</svg>
<div class="abs brand"><span class="dot"></span>Brightvale Clean</div>
<nav class="abs nav">
  <span class="active">Home</span><span>About Us</span><span>Services</span><span>Commercial</span><span>Schedule a Job</span><span>Referral Program</span><span>Contact Us</span>
</nav>

<svg class="abs arrow" style="left:46px" viewBox="0 0 24 44" aria-hidden="true"><polyline points="20,4 4,22 20,40" fill="none" stroke="#fff" stroke-width="3"/></svg>
<svg class="abs arrow" style="left:1130px" viewBox="0 0 24 44" aria-hidden="true"><polyline points="4,4 20,22 4,40" fill="none" stroke="#fff" stroke-width="3"/></svg>

<div class="abs caption">
  <div class="l1">Professional <b>Cleaners</b> of</div>
  <div class="l2">Carpets, Rugs, Floors <span style="font-weight:300">and</span> Fine Fabrics</div>
</div>

<svg class="abs service-area" viewBox="0 0 1200 100" aria-hidden="true">
  <polygon points="0,0 0,100 1200,100 1200,0 1180,36 20,36" fill="#fff"/>
  <polygon points="0,0 20,36 1180,36 1200,0 1200,20 1150,98 50,98 0,20" fill="#2b63a8"/>
  <polygon points="20,36 1180,36 1150,98 50,98" fill="var(--blue)"/>
</svg>
<div class="abs service-text">SERVICING CAIRNS AND SURROUNDING FAR NORTH QUEENSLAND. INNISFAIL, MAREEBA TO MOSSMAN.</div>

<h2 class="sec" style="top:764px">Our <span>Services</span></h2>
<div class="abs view-all">View All &raquo;</div>

<div class="abs card" style="left:138px">
  <div class="icon"><i style="background:#c7553a" role="img" aria-label="Rolled carpet"></i></div>
  <h3>CARPET CLEANING</h3>
  <p>Consectetuer adipiscing elit. Aenean commodo ligula eget dolor. Aenean massa. Cum sociis natoque penatibus et magnis dis parturient montes, nascetur ridiculus mus.</p>
</div>
<div class="abs divider" style="left:447px"></div>
<div class="abs card" style="left:439px">
  <div class="icon"><i style="background:#9a9a8e" role="img" aria-label="Stone tile"></i></div>
  <h3>TILES CLEANING</h3>
  <p>Consectetuer adipiscing elit. Aenean commodo ligula eget dolor. Aenean massa. Cum sociis natoque penatibus et magnis dis parturient montes, nascetur ridiculus mus.</p>
</div>
<div class="abs divider" style="left:753px"></div>
<div class="abs card" style="left:757px">
  <div class="icon"><i style="background:#b8773c" role="img" aria-label="Timber floor plank"></i></div>
  <h3>FLOORS CLEANING</h3>
  <p>Consectetuer adipiscing elit. Aenean commodo ligula eget dolor. Aenean massa. Cum sociis natoque penatibus et magnis dis parturient montes, nascetur ridiculus mus.</p>
</div>

<section class="abs signup">
  <p>Signup for our new exclusive internet offers and save $$$</p>
  <span class="btn">Signup Now</span>
</section>

<div class="abs social-box">
  <span class="sq"></span>
  <div class="find">Find us on:<br>our social page</div>
  <span class="sep"></span>
  <div class="offer">10% Discount on all services<br>on top of ant other offer</div>
</div>
<div class="abs news">
  <h4>NEWS LETTER SIGNUP</h4>
  <div class="field">Email</div>
  <div class="send">SEND</div>
</div>

<h2 class="sec" style="top:1464px">About <span>Brightvale Clean</span></h2>
<p class="abs about">Brightvale Clean is a professional, full-service carpet, floor, fabric care company serving the North Queensland areas including Cairns, Tablelands, Port Douglas and Mission Beach. Brightvale Carpet Cleaning has been in business since 1996. At Brightvale Clean, we take pride in our reputation, experience, education, systems, and guarantee. Brightvale Clean is an NCRB certified firm, the world's most recognized body of certification for carpet and upholstery cleaners. You can depend on us at Brightvale Carpet Cleaning Services for carpet cleaning, upholstery cleaning, oriental and area rug cleaning, fiber and fabric protection, tile and grout cleaning and sealing, natural stone, hardwood care, drapery cleaning and urine damage treatment.</p>

<div class="abs tile" style="left:142px;background:linear-gradient(160deg,#5b7590,#9fb3c4 50%,#3e4f60)" role="img" aria-label="Service van parked outside a building">
  <div class="tl" style="top:88px">Shedule your Cleaning Today</div><span class="btn">Click Here</span>
</div>
<div class="abs tile" style="left:376px;background:linear-gradient(160deg,#b99a7b,#e4cdb2 50%,#d8b896)" role="img" aria-label="Toddler crawling on a clean tiled floor">
  <div class="tl" style="top:32px;text-align:left;padding-left:12px">Introductory<br>Offer !</div><span class="btn">Click Here</span>
</div>
<div class="abs tile" style="left:610px;background:linear-gradient(160deg,#b07a4c,#8c5a34 60%,#6d4526)" role="img" aria-label="Timber floor with a large tick">
  <div class="tl" style="top:40px">6 Reasons to choose<br>Brightvale Clean<br>over any other cleaner</div><span class="btn">Click Here</span>
</div>
<div class="abs tile" style="left:843px;background:linear-gradient(180deg,#e8eef2,#8fb7cf 45%,#2f86c0)" role="img" aria-label="House standing in flood water">
  <div class="tl" style="top:96px">Water Damage !</div><span class="btn" style="top:128px">Click Here</span>
</div>

<footer>
  <div class="abs footer-top"></div>
  <div class="abs badge-sq" role="img" aria-label="Certification badge"></div>
  <div class="abs badge-cap">Certified Firm</div>
  <div class="abs badge-seal" role="img" aria-label="Over 25 years seal"></div>
  <div class="abs contact">Flood &amp; Water Damage<br>24/7 Service<br>Quick Drying Systems<br>Insurance Work Welcome<br>Phone 4000 1234<br>0400 555 017<br>PO Box 212 Harbourside Qld 4870</div>
  <div class="abs f-brand">Brightvale Clean<span class="dot"></span></div>
  <div class="abs tagline">we don't cut corners - we clean them.</div>
  <div class="abs partners" role="img" aria-label="Partner badges"><i></i><i></i><i></i><i></i></div>
  <svg class="abs" style="left:588px;top:2161px" width="24" height="13" viewBox="0 0 24 13" aria-hidden="true"><polygon points="0,13 12,0 24,13" fill="var(--blue)"/></svg>
  <div class="abs footer-bottom">
    <p>&copy; ALL RIGHTS RESERVED 2014 - BRIGHTVALECLEAN</p>
    <div class="socials"><i></i><i></i><i></i><i></i></div>
  </div>
</footer>

</body>
</html>
```